Condo Debts Collection Business needs a Web Design (Contest)

I need a site for a client, who works with condo debts collection, and ensure all revenues provided by condo fees will be always available to the building manager of condo on a specific date, regardless of defaults.I have the logo of the companies, and some requirements on layout (kind of slider, menu options, phone number on a noble position, etc).
Updates

Designs look the same

Target Market(s)

I have two targets for this design: - Condominium's building manager. This target is looking for a solution to overdue debts on it's condo. - Residents on condominiums. This target wants to live in a better place, where their neighbors pay their condominium fees on time.

Number of Pages Required

1 page

Requirements
Must have
• - Slider with title, some short text related, a nice image (I prefer happy and/or peaceful family, people doing business, happy friends, and so on).
• - I have a special attention to menu. I'm looking for one I can have a nice effect, more elegant, charming, kind of innovative.
• - Phone number on the top (or clearly visible).
• - Member log in area or icon on the top (or clearly visible).
• - News/articles area.
• - Modern fonts, with good quality, sans-serif on areas where reading is more intensive (prefer Google web-fonts).
• - Colors specified on attached files.
• - Header similar or inspired by the "FILE 3"
Nice to have
• - Clear background color, cause it's better to read larger texts (like articles). Dark backgrounds makes reading difficult.
• - A site with effects (like shadows, lines, gradients, lights) is usually pretty.
• - I pay attention on beautiful footers.
Should not have
• - Images with a lot of money (I don't sell richness, I sell tranquility, peace, harmony, safety).
• - Poor menu.
• - Lots of curves. My customer asked for straight lines.

```html
<!DOCTYPE html>
<html lang="en">
<head>
<meta charset="utf-8">
<title>Serenova – Condo Fee Assurance</title>
<link href="https://fonts.googleapis.com/css2?family=Bree+Serif&family=Lato:wght@400;700;900&display=swap" rel="stylesheet">
<style>
:root{
  --navy:#17336e;
  --navy-deep:#112a5c;
  --orange:#d9621a;
  --orange-light:#ec7a2b;
  --grey-bg:#eeeeee;
  --footer-bg:#e9e9e9;
  --text:#555555;
  --heading:#222222;
  --white:#ffffff;
  --line:#d0d0d0;
}
*{margin:0;padding:0;box-sizing:border-box}
html,body{width:1200px;height:4489px;overflow:hidden}
body{position:relative;background:var(--white);font-family:"Lato",sans-serif;color:var(--text)}
.abs{position:absolute}
h1,h2,h3,.serif{font-family:"Bree Serif",serif;font-weight:400}

/* header */
.site-header{left:0;top:0;width:1200px;height:120px;background:var(--navy)}
.brand{left:170px;top:22px;display:flex;align-items:center;gap:12px;color:var(--white);font-family:"Bree Serif",serif;font-size:34px}
.brand .mark{width:22px;height:22px;background:var(--orange)}
.phone{left:596px;top:22px;color:var(--white);font-size:21px;display:flex;align-items:center;gap:6px;white-space:nowrap}
.member-btn{left:862px;top:18px;width:162px;height:36px;border-radius:18px;background:linear-gradient(var(--orange-light),var(--orange));color:var(--white);font-size:13px;font-weight:700;display:flex;align-items:center;justify-content:center;gap:8px;letter-spacing:.5px;white-space:nowrap}
.main-nav{left:435px;top:72px;display:flex;gap:0}
.main-nav a{color:var(--white);text-decoration:none;font-size:15px;font-weight:700;padding:0 20px;position:relative;white-space:nowrap}
.main-nav a.active::after{content:"";position:absolute;left:6px;right:6px;bottom:-10px;height:3px;background:var(--orange)}

/* hero */
.hero{left:0;top:120px;width:1200px;height:598px;background:linear-gradient(160deg,#f2c66a 0%,#d98a3a 40%,#8a5a2b 75%,#4e3620 100%)}
.hero-title{left:742px;top:329px;width:285px;height:56px;background:var(--navy);color:var(--white);font-family:"Bree Serif",serif;font-size:40px;text-align:right;padding-right:14px;line-height:56px}
.hero-text{left:614px;top:389px;width:413px;height:126px;background:var(--orange);color:var(--white);font-size:17px;font-weight:700;text-align:right;padding:22px 16px;line-height:1.45}
.dots{left:566px;top:636px;display:flex;gap:6px}
.dots i{width:12px;height:12px;border-radius:50%;background:var(--white);opacity:.7}
.dots i:first-child{opacity:1}

/* section headings */
.section-title{width:1200px;left:0;text-align:center;color:var(--heading);font-size:46px}
.section-lead{left:250px;width:700px;text-align:center;font-size:12.5px;line-height:22px}

/* welcome */
.welcome{left:0;top:718px;width:1200px;height:584px;background:var(--grey-bg)}
.card{background:var(--white);box-shadow:0 6px 14px rgba(0,0,0,.18);text-align:center;overflow:hidden}
.card .photo{height:224px}
.card h3{font-family:"Lato",sans-serif;font-weight:900;font-size:17px;color:var(--heading);margin:28px 0 14px}
.card p{font-size:12.5px;line-height:21px;padding:0 34px}

/* who */
.who-photo{left:0;top:1437px;width:599px;height:610px;background:linear-gradient(135deg,#efe9e2 0%,#c9b9a6 50%,#7d6250 100%)}
.who-title{left:635px;top:1541px;font-size:46px;color:var(--heading)}
.who-text{left:646px;top:1616px;width:455px;font-size:12px;line-height:19.5px}
.who-text p+p{margin-top:20px}
.btn{height:32px;border-radius:16px;background:linear-gradient(var(--orange-light),var(--orange));color:var(--white);font-size:12px;font-weight:700;display:flex;align-items:center;justify-content:center;letter-spacing:.5px}

/* what */
.what{left:0;top:2047px;width:1200px;height:677px;background:var(--grey-bg)}
.service{background:var(--white);box-shadow:0 10px 14px rgba(0,0,0,.15);text-align:center;padding-top:42px}
.service h3{font-family:"Lato",sans-serif;font-weight:900;font-size:17px;color:var(--heading);margin:34px 0 10px}
.service p{font-size:12.5px;line-height:21px;padding:0 24px}

/* articles */
.article{text-align:left}
.article .photo{height:195px}
.article .date{font-size:12px;color:var(--orange);font-weight:700;margin:16px 0 0 30px;padding:0}
.article h3{font-family:"Bree Serif",serif;color:var(--navy);font-size:18px;line-height:22px;margin:8px 30px 10px}
.article p{font-size:12.5px;line-height:21px;padding:0 30px}

/* testimonials / locations */
.testimonials{left:0;top:3538px;width:600px;height:524px;background:var(--orange)}
.locations{left:600px;top:3538px;width:600px;height:524px;background:var(--navy)}
.band-title{font-size:44px;color:var(--white)}
.band-text{font-size:12.5px;line-height:22px;color:var(--white)}
.location-img{height:171px;position:absolute;top:263px}
.location-img span{position:absolute;left:16px;bottom:12px;color:var(--white);font-family:"Bree Serif",serif;font-size:17px}

/* footer */
.site-footer{left:0;top:4062px;width:1200px;height:368px;background:var(--footer-bg)}
.footer-col{top:88px}
.footer-col h4{font-size:16px;color:var(--heading);font-weight:700;margin-bottom:14px;display:flex;align-items:center;gap:10px}
.footer-col p,.footer-col li{font-size:12.5px;line-height:20px;list-style:none;color:#444}
.divider{top:0;width:1px;height:368px;background:var(--line)}
.social{display:flex;gap:20px;margin-top:4px}
.social i{width:22px;height:22px;border-radius:50%;background:#666}
.footer-brand{display:flex;align-items:center;gap:10px;font-family:"Bree Serif",serif;font-size:32px;color:var(--navy)}
.footer-brand .mark{width:20px;height:20px;background:var(--navy)}
.bottom-bar{left:0;top:4430px;width:1200px;height:59px;background:var(--white);font-size:12px;text-align:center;line-height:59px;color:#444}
</style>
</head>
<body>

<header class="site-header abs">
  <div class="brand abs"><span class="mark"></span>Serenova</div>
  <div class="phone abs">
    <svg width="20" height="20" viewBox="0 0 24 24"><path fill="#fff" d="M6.6 10.8a15 15 0 0 0 6.6 6.6l2.2-2.2c.3-.3.7-.4 1-.2 1.1.4 2.3.6 3.6.6.6 0 1 .4 1 1V20c0 .6-.4 1-1 1A17 17 0 0 1 3 4c0-.6.4-1 1-1h3.5c.6 0 1 .4 1 1 0 1.3.2 2.5.6 3.6.1.3 0 .7-.2 1z"/></svg>
    Phone: (85) 555 0 1 23
  </div>
  <div class="member-btn abs">
    <svg width="12" height="14" viewBox="0 0 12 14"><rect x="1" y="6" width="10" height="8" fill="#fff"/><path d="M3 6V4a3 3 0 0 1 6 0v2" stroke="#fff" stroke-width="1.6" fill="none"/></svg>
    MEMBER LOG IN
  </div>
  <nav class="main-nav abs">
    <a class="active">Home</a><a>About</a><a>Services ▾</a><a>Why Choose us?</a><a>Faq</a><a>Contact Us</a>
  </nav>
</header>

<section class="hero abs" role="img" aria-label="Photo of a happy family running through a golden field at sunset"></section>
<h1 class="hero-title abs">Serenova</h1>
<div class="hero-text abs">Sed ut unde omnis iste natus voluptatem accusa ntium doloremque laudant ium, iste natus voluptatem cusantium doloremque unde omnis</div>
<div class="dots abs"><i></i><i></i><i></i><i></i></div>

<section class="welcome abs">
  <h2 class="section-title abs serif" style="top:52px">Welcome to Serenova</h2>
  <p class="section-lead abs" style="top:124px">Sed ut perspiciatis unde omnis iste natus error sit voluptatem accusantium doloremque laudantium, totam rem aperiam, eaque ipsa quae ab illo inventore veritatis et quasi architecto beatae vitae dicta sunt, totam rem aperiam, eaque ipsa quae ab</p>
  <article class="card abs" style="left:174px;top:195px;width:269px;height:389px">
    <div class="photo" role="img" aria-label="Photo of hands reviewing documents with a calculator" style="background:linear-gradient(135deg,#dfe6ee,#8ea4bf)"></div>
    <h3>Serspiciatnd</h3>
    <p>Sectetis unde omnis iste natl volupta tem accusantium doloremqu nitum, totlatis unde omnis iste natl tugit atem accusantium doloreqoueula.</p>
  </article>
  <article class="card abs" style="left:464px;top:195px;width:269px;height:389px">
    <div class="photo" role="img" aria-label="Photo of a family working together at a kitchen table" style="background:linear-gradient(135deg,#f1ece4,#b59b82)"></div>
    <h3>Serspiciatnd</h3>
    <p>Sectetis unde omnis iste natl volupta tem accusantium doloremqu nitum, totlatis unde omnis iste natl tugit atem accusantium doloreqoueula.</p>
  </article>
  <article class="card abs" style="left:757px;top:195px;width:270px;height:389px">
    <div class="photo" role="img" aria-label="Photo of business people discussing papers in an office" style="background:linear-gradient(135deg,#e8e2d6,#6f7b8c)"></div>
    <h3>Serspiciatnd</h3>
    <p>Sectetis unde omnis iste natl volupta tem accusantium doloremqu nitum, totlatis unde omnis iste natl tugit atem accusantium doloreqoueula.</p>
  </article>
</section>

<div class="who-photo abs" role="img" aria-label="Photo of smiling friends gathered around a laptop at home"></div>
<h2 class="who-title abs">Who We Are</h2>
<div class="who-text abs">
  <p>Sed ut perspiciatis unde omnis iste natus error sit voluptatem accusantium doloremque laudantium, totam rem aperiam, eaque ipsa quae ab illo inventore veritatis et quasi architecto beatae vitae dicta sunt, totam rem aperiam, eaque ipsa quae ut perspiciatis unde omnis iste natus error sit voluptatem accusantium doloremque laudantium, totam rem aperiam, eaque ipsa quae ab illo inventore veritatis et quasi architecto.</p>
  <p>Sed ut perspiciatis unde omnis iste natus error sit voluptatem accusantium doloremque laudantium, totam rem aperiam, eaque ipsa quae ab illo inventore veritatis et quasi architecto beatae vitae dicta sunt, totam rem aperiam, eaque ipsa quae ut perspiciatis unde omnis iste natus error sit voluptatem accusantium doloremque laudan.</p>
</div>
<div class="btn abs" style="left:643px;top:1908px;width:123px">READ MORE</div>

<section class="what abs">
  <h2 class="section-title abs serif" style="top:108px">What We Do</h2>
  <p class="section-lead abs" style="top:178px">Sed ut perspiciatis unde omnis iste natus error sit voluptatem accusantium doloremque laudantium, totam rem aperiam, eaque ipsa quae ab illo inventore veritatis et quasi architecto beatae vitae dicta sunt, totam rem aperiam, eaque ipsa quae ab</p>

  <div class="service abs" style="left:165px;top:258px;width:203px;height:275px">
    <svg width="64" height="58" viewBox="0 0 64 58"><path d="M6 28 32 6l26 22" fill="none" stroke="#17336e" stroke-width="4"/><rect x="14" y="26" width="36" height="28" fill="#d9621a" stroke="#17336e" stroke-width="3"/><rect x="27" y="36" width="10" height="18" fill="#fff" stroke="#17336e" stroke-width="2"/></svg>
    <h3>Serspiciatnd</h3>
    <p>Sectetis unde omnis iste natl voluptatem accusantium dolorque audentium, totam remis.</p>
  </div>
  <div class="service abs" style="left:386px;top:258px;width:204px;height:275px">
    <svg width="64" height="58" viewBox="0 0 64 58"><path d="M32 4a14 14 0 0 1 14 14c0 11-14 24-14 24S18 29 18 18A14 14 0 0 1 32 4z" fill="#d9621a" stroke="#17336e" stroke-width="3"/><circle cx="32" cy="18" r="5" fill="#fff" stroke="#17336e" stroke-width="2"/><path d="M10 54h44" stroke="#17336e" stroke-width="4"/></svg>
    <h3>Serspiciatnd</h3>
    <p>Sectetis unde omnis iste natl voluptatem accusantium dolorque audentium, totam remis.</p>
  </div>
  <div class="service abs" style="left:608px;top:258px;width:203px;height:275px">
    <svg width="64" height="58" viewBox="0 0 64 58"><path d="M20 22 38 6l18 16" fill="none" stroke="#17336e" stroke-width="4"/><rect x="26" y="20" width="24" height="20" fill="#d9621a" stroke="#17336e" stroke-width="3"/><circle cx="16" cy="36" r="6" fill="#17336e"/><path d="M4 56c0-9 5-13 12-13s12 4 12 13z" fill="#17336e"/></svg>
    <h3>Serspiciatnd</h3>
    <p>Sectetis unde omnis iste natl voluptatem accusantium dolorque audentium, totam remis.</p>
  </div>
  <div class="service abs" style="left:829px;top:258px;width:207px;height:275px">
    <svg width="64" height="58" viewBox="0 0 64 58"><path d="M22 20 38 6l16 14" fill="none" stroke="#17336e" stroke-width="4"/><rect x="27" y="18" width="22" height="16" fill="#d9621a" stroke="#17336e" stroke-width="3"/><path d="M4 44h14l10 4h18l10-8" fill="none" stroke="#17336e" stroke-width="4"/></svg>
    <h3>Serspiciatnd</h3>
    <p>Sectetis unde omnis iste natl voluptatem accusantium dolorque audentium, totam remis.</p>
  </div>
</section>

<h2 class="section-title abs serif" style="top:2812px">Latest Articles</h2>
<p class="section-lead abs" style="top:2882px">Sed ut perspiciatis unde omnis iste natus error sit voluptatem accusantium doloremque laudantium, totam rem aperiam, eaque ipsa quae ab illo inventore veritatis et quasi architecto beatae vitae dicta sunt, totam rem aperiam, eaque ipsa quae ab</p>

<article class="card article abs" style="left:174px;top:2963px;width:269px;height:398px">
  <div class="photo" role="img" aria-label="Photo of two businessmen shaking hands in an office" style="background:linear-gradient(135deg,#e4e9ef,#7b8ea6)"></div>
  <p class="date">Mai 10 2019</p>
  <h3>Serpi lorem usimf ciatn dlorwm lorekm</h3>
  <p>Sectetis unde omnis iste natl volupta tem accusantium doloremqu nitum, totlatis unde omnis iste natl tugit atem accusantium doloreqoueula.</p>
</article>
<article class="card article abs" style="left:464px;top:2963px;width:269px;height:398px">
  <div class="photo" role="img" aria-label="Photo of a couple meeting an adviser in a bright office" style="background:linear-gradient(135deg,#eef1f2,#8f9aa5)"></div>
  <p class="date">Mai 10 2019</p>
  <h3>Serpi lorem usimf ciatn dlorwm lorekm</h3>
  <p>Sectetis unde omnis iste natl volupta tem accusantium doloremqu nitum, totlatis unde omnis iste natl tugit atem accusantium doloreqoueula.</p>
</article>
<article class="card article abs" style="left:757px;top:2963px;width:270px;height:398px">
  <div class="photo" role="img" aria-label="Photo of an older couple signing papers with an agent" style="background:linear-gradient(135deg,#f0e8dc,#9a8069)"></div>
  <p class="date">Mai 10 2019</p>
  <h3>Serpi lorem usimf ciatn dlorwm lorekm</h3>
  <p>Sectetis unde omnis iste natl volupta tem accusantium doloremqu nitum, totlatis unde omnis iste natl tugit atem accusantium doloreqoueula.</p>
</article>
<div class="btn abs" style="left:539px;top:3397px;width:122px">READ MORE</div>

<section class="testimonials abs">
  <h2 class="band-title abs" style="left:174px;top:80px">Testimonials</h2>
  <svg class="abs" style="left:506px;top:100px" width="24" height="14" viewBox="0 0 24 14"><path d="M7 2 2 7l5 5M17 2l5 5-5 5" fill="none" stroke="#fff" stroke-width="2"/></svg>
  <svg class="abs" style="left:174px;top:172px" width="22" height="18" viewBox="0 0 22 18"><path d="M0 18V9L5 0h4L6 8h4v10zm12 0V9l5-9h4l-3 8h4v10z" fill="#fff"/></svg>
  <p class="band-text abs" style="left:210px;top:170px;width:345px">Sed ut perspiciatis unde omnis iste natus error sit voluptatem accusantium doloremque laudantium, totam rem aperiam, eaque ipsa quae ab illo inventore veritatis et quasi architecto beatae vitae dictase. totam rem aperiam, eaque ipsa quae ab illo sed ut perspiciatis unde omnis iste natus error sit voluptatem accusantium doloremque laudantium, totam rem aperiam, eaque ipsa quae ab illo inventore veritatis et quasi architecto beatae vitae dicta sunt.</p>
  <div class="btn abs" style="left:210px;top:368px;width:107px;height:26px;background:#fff;color:var(--orange)">READ MORE</div>
  <p class="band-text abs" style="left:225px;top:418px;font-weight:700;font-style:italic">_Ana Ruiz , City Name</p>
</section>

<section class="locations abs">
  <h2 class="band-title abs" style="left:32px;top:80px">Locations</h2>
  <p class="band-text abs" style="left:32px;top:170px;width:400px">Sed ut perspiciatis unde omnis iste natus error sit voluptatecusantium d oloremque laudantium, totam rem aperiam, eaque ipsa quae ab illo inve ntore veritatis et quasi architecto beatae vitae dictae totam.</p>
  <div class="location-img" role="img" aria-label="Photo of a city skyline at dusk" style="left:32px;width:188px;background:linear-gradient(#f0a36a,#5a4a6a 60%,#2c2c3e)"><span>Location Name</span></div>
  <div class="location-img" role="img" aria-label="Photo of downtown towers at sunset" style="left:235px;width:192px;background:linear-gradient(#c9a68a,#6a6f86 55%,#2e3446)"><span>Location Name</span></div>
</section>

<footer class="site-footer abs">
  <div class="divider abs" style="left:359px"></div>
  <div class="divider abs" style="left:584px"></div>
  <div class="divider abs" style="left:802px"></div>
  <div class="footer-col abs" style="left:174px">
    <h4><svg width="14" height="18" viewBox="0 0 14 18"><path d="M7 1a6 6 0 0 1 6 6c0 5-6 10-6 10S1 12 1 7a6 6 0 0 1 6-6z" fill="none" stroke="#555" stroke-width="1.6"/><circle cx="7" cy="7" r="2" fill="#555"/></svg>Address</h4>
    <p>Norvale<br>Lorem Ipsumstraat 42,<br>1200 AB, Veltharum<br>Dummy lorem ivtr</p>
    <h4 style="margin-top:22px"><svg width="18" height="14" viewBox="0 0 18 14"><rect x="1" y="1" width="16" height="12" fill="none" stroke="#555" stroke-width="1.6"/><path d="m1 1 8 7 8-7" fill="none" stroke="#555" stroke-width="1.6"/></svg>Email</h4>
    <p>info@serenova.com</p>
    <h4 style="margin-top:22px"><svg width="16" height="16" viewBox="0 0 24 24"><path fill="#555" d="M6.6 10.8a15 15 0 0 0 6.6 6.6l2.2-2.2c.3-.3.7-.4 1-.2 1.1.4 2.3.6 3.6.6.6 0 1 .4 1 1V20c0 .6-.4 1-1 1A17 17 0 0 1 3 4c0-.6.4-1 1-1h3.5c.6 0 1 .4 1 1 0 1.3.2 2.5.6 3.6.1.3 0 .7-.2 1z"/></svg>Phone</h4>
    <p>030-5550199</p>
  </div>
  <div class="footer-col abs" style="left:422px">
    <h4>Links</h4>
    <ul><li>Lorem ipsum dolor</li><li>Consectetur adipiscin</li><li>Do eiusmodt</li></ul>
    <h4 style="margin-top:22px">Information</h4>
    <ul><li>About Us</li><li>Imprint</li><li>Contact</li><li>News</li></ul>
  </div>
  <div class="footer-col abs" style="left:643px">
    <h4>More Info</h4>
    <ul><li>Lorem ipsum dolor</li><li>Consectetur adipiscin</li><li>Do eiusmodt</li><li>Lorem ipsum dolor</li><li>Consectetur adipiscin</li><li>Do eiusmodt</li><li>Lorem ipsum dolor</li><li>Consectetur adipiscin</li><li>Do eiusmodt</li></ul>
  </div>
  <div class="footer-col abs" style="left:859px">
    <h4>Follow Us</h4>
    <div class="social"><i></i><i></i><i></i><i></i></div>
  </div>
  <div class="footer-brand abs" style="left:836px;top:270px"><span class="mark"></span>Serenova</div>
</footer>

<div class="bottom-bar abs">© 2019 Serenova. All rights reserved.</div>

</body>
</html>
```